Maple Bus Card

i own a building in the bronx ny - its called "Maple 7 on 2 HDFC"i want a classy logo / business card - nothing too religuous but it is like a family there - its a large apartment building - colors i like dark red, black, medium shade of gray also reg business card stuff tel # 914-555-0173 address 4738 Larkwell Ave Bronx NY 10460 Email fijosh@aol.comslogan - " from many we are one "i can send u a picture of the building for the backside

```html
<!DOCTYPE html>
<html lang="en">
<head>
<meta charset="utf-8">
<title>Maple 7 on 2 HDFC – Business Card</title>
<link href="https://fonts.googleapis.com/css2?family=Roboto:wght@400;500;700&family=Open+Sans:wght@400&display=swap" rel="stylesheet">
<style>
  :root {
    --canvas-gray: #999999;
    --card-black: #0b0c0c;
    --gold: #f3b51b;
    --slogan-gray: #b9b9b9;
    --detail-white: #f2f2f2;
    --title-gray: #c9c9c9;
    --brick-dark: #5a2a22;
    --brick: #7a3c2f;
    --foliage: #2f4a26;
    --street: #4a4a48;
  }
  * { margin: 0; padding: 0; box-sizing: border-box; }
  html, body { width: 1200px; height: 900px; overflow: hidden; }
  body { background: var(--canvas-gray); position: relative; font-family: "Roboto", sans-serif; }

  .card {
    position: absolute;
    top: 275px;
    width: 478px;
    height: 295px;
    box-shadow: 2px 3px 6px rgba(0, 0, 0, 0.35);
    overflow: hidden;
  }
  .card-front {
    left: 120px;
    background: var(--card-black);
    border-radius: 0 46px 0 46px;
  }
  .card-back {
    left: 607px;
    border-radius: 46px 0 46px 0;
  }

  .brand {
    position: absolute;
    left: 30px;
    top: 40px;
    width: 200px;
    text-align: center;
  }
  .brand-mark {
    width: 22px;
    height: 22px;
    margin: 0 auto 70px;
    background: var(--gold);
  }
  .brand-name {
    color: var(--gold);
    font-family: "Roboto", sans-serif;
    font-weight: 500;
    font-size: 21px;
    line-height: 26px;
    letter-spacing: 0.5px;
  }
  .brand-rule {
    height: 1px;
    background: var(--slogan-gray);
    margin: 6px 4px 0;
  }
  .slogan {
    position: absolute;
    left: 33px;
    top: 195px;
    color: var(--slogan-gray);
    font-weight: 500;
    font-size: 15.5px;
    letter-spacing: 0.1px;
  }

  .contact {
    position: absolute;
    left: 277px;
    top: 146px;
    font-family: "Open Sans", sans-serif;
    color: var(--detail-white);
  }
  .contact-name {
    font-family: "Roboto", sans-serif;
    font-weight: 700;
    color: var(--gold);
    font-size: 18.5px;
    line-height: 24px;
  }
  .contact-title {
    color: var(--title-gray);
    font-size: 13.5px;
    line-height: 18px;
    margin-bottom: 7px;
  }
  .contact-line {
    display: flex;
    align-items: center;
    gap: 6px;
    font-size: 13.5px;
    line-height: 18px;
  }
  .contact-line svg { width: 13px; height: 11px; fill: var(--gold); flex: none; }
  .contact-address {
    font-size: 13.5px;
    line-height: 17px;
    margin-top: 6px;
  }

  .building-photo {
    width: 100%;
    height: 100%;
    background:
      linear-gradient(180deg, rgba(0,0,0,0) 78%, var(--street) 100%),
      linear-gradient(90deg, var(--foliage) 0%, var(--foliage) 30%, var(--brick-dark) 42%, var(--brick) 70%, var(--brick-dark) 100%);
  }
</style>
</head>
<body>
  <section class="card card-front">
    <div class="brand">
      <div class="brand-mark"></div>
      <div class="brand-name">Maple 7 on 2 HDFC</div>
      <div class="brand-rule"></div>
    </div>
    <p class="slogan">FROM MANY WE ARE ONE</p>

    <div class="contact">
      <div class="contact-name">DANIEL REYES</div>
      <div class="contact-title">Managing Director</div>
      <div class="contact-line">
        <svg viewBox="0 0 13 11" aria-hidden="true"><path d="M1 3 Q6.5 -1 12 3 L12 4.5 L9.5 4.5 L9 3.2 Q6.5 2.5 4 3.2 L3.5 4.5 L1 4.5 Z M3 5.5 L10 5.5 L11.5 10.5 L1.5 10.5 Z"/></svg>
        <span>914-555-0173</span>
      </div>
      <div class="contact-line">
        <svg viewBox="0 0 13 11" aria-hidden="true"><path d="M1 2 L12 2 L12 10 L1 10 Z M1.8 2.8 L6.5 6.5 L11.2 2.8 Z" fill-rule="evenodd"/></svg>
        <span>mavreld@quintmail.com</span>
      </div>
      <div class="contact-address">4738 Larkwell Ave<br>Bronx NY 10460</div>
    </div>
  </section>

  <section class="card card-back">
    <div class="building-photo" role="img" aria-label="Photograph of the red-brick apartment building on a street in the Bronx, with a tree at left and parked cars in front"></div>
  </section>
</body>
</html>
```